Online interactive calendar for training organisation

We have a new website being made and need a design for an online calendar that is interactive and very simple and easy to use. On our main page this calendar will include all of our courses (approx 30 different ones with up to 8 different locations). On our sub pages which have course information, the calendar will only include details of that specific course. Details needed are: Course code, course name/title, date, duration (1/2 day - 5 days), location, price, discount price. Maybe also a key for available or limited spots left? We want a section at the top of the calendar to be able to filter by location or course, and maybe to filter by month also? I have included a spreadsheet with a sample of our courses with this information. Also a sample draft of the main page on our new webpage to show the colour green which is our company colour. Main notes - we want as simple, effective and easy to use as possible.
We will need to know what plug in we can use to get the design you have created.

Target Market(s)

Mining and construction - both companies and individuals

Number of Pages Required

1 page

Colors
cadf82

Requirements
Must have
• Be simple, easy to use, effective.

```html
<!DOCTYPE html>
<html lang="en">
<head>
<meta charset="utf-8">
<title>Ridgeline Safety – Training Calendar</title>
<link href="https://fonts.googleapis.com/css2?family=Montserrat:wght@400;500;600;700&family=Lato:wght@400;700&display=swap" rel="stylesheet">
<style>
:root{
  --green:#cadf82;
  --green-text:#9fbf2e;
  --dark:#2b2b2b;
  --ink:#222;
  --muted:#555;
  --line:#e2e2e2;
  --white:#fff;
  --red:#d3201f;
  --panel:#efefef;
}
*{box-sizing:border-box;margin:0;padding:0}
html,body{width:1200px;height:2655px;overflow:hidden}
body{position:relative;background:var(--white);font-family:"Montserrat",sans-serif;color:var(--ink)}
.abs{position:absolute}

/* top bar */
.topbar{left:0;top:0;width:1200px;height:44px;background:var(--green)}
.social-top{left:112px;top:13px;display:flex;gap:4px}
.social-top span{width:14px;height:14px;border-radius:50%;background:#111;display:block}
.student-btn{left:902px;top:12px;width:80px;height:20px;background:#1d1d1d;color:#fff;font-size:8px;font-weight:700;border-radius:3px;display:flex;align-items:center;justify-content:center}
.search-box{left:988px;top:12px;width:100px;height:20px;background:#fff;border-radius:2px}
.search-box svg{position:absolute;right:8px;top:5px}

/* header */
.header{left:0;top:44px;width:1200px;height:102px;background:#fff}
.brand{left:112px;top:66px;display:flex;align-items:center;gap:10px}
.brand-mark{width:44px;height:44px;border-radius:50%;background:var(--red)}
.brand-name{font-weight:700;font-size:21px;color:var(--red);letter-spacing:.5px;line-height:1}
.brand-tag{font-size:9.5px;font-weight:600;color:#333;margin-top:6px;letter-spacing:.4px;padding-left:26px}
.nav{right:112px;top:73px;display:flex;gap:6px;font-size:16px;font-weight:500}
.nav a{color:#222;text-decoration:none;padding:8px 14px;border-radius:3px}
.nav a.active{background:var(--green)}

/* hero */
.hero{left:0;top:146px;width:1200px;height:514px;background:linear-gradient(120deg,#8b7c63 0%,#a99a80 30%,#7a7770 55%,#3c4a5c 80%,#2e3844 100%)}
.hero-title{left:0;top:290px;width:1200px;text-align:center;color:#fff}
.hero-title h1{font-size:52px;font-weight:700;line-height:1.1}
.hero-title p{font-size:44px;font-weight:500;line-height:1.2}

/* card */
.card{background:#fff;border-radius:38px 38px 30px 30px;box-shadow:0 2px 10px rgba(0,0,0,.12);overflow:hidden}
.card-head{height:78px;background:var(--green);color:#fff;font-size:30px;font-weight:700;display:flex;align-items:center;justify-content:center;letter-spacing:.3px}
.diff{left:112px;top:518px;width:976px;height:625px}
.diff-sub{text-align:center;font-size:17px;margin-top:28px;color:#333}
.tiles{position:absolute;left:14px;top:165px;display:grid;grid-template-columns:repeat(5,184px);gap:10px 7px}
.tile{height:204px;border:2px solid #ddd;display:flex;flex-direction:column}
.tile-photo{height:146px}
.tile-label{flex:1;display:flex;align-items:center;justify-content:center;text-align:center;font-size:17px;font-weight:600;line-height:1.1;padding:0 6px}

/* calendar */
.calendar{left:112px;top:1200px;width:976px;height:735px}
.filters{position:absolute;left:19px;top:109px;width:939px;height:88px;background:var(--panel);border:2px solid #ddd;border-radius:3px}
.select{position:absolute;top:19px;width:291px;height:48px;background:#fff;border:1px solid #ccc;border-radius:3px;display:flex;align-items:center;padding-left:14px;gap:8px;font-size:19px;color:#777}
.select::after{content:"";position:absolute;right:14px;top:21px;border:4px solid transparent;border-top:5px solid #444}
.dropdown{left:301px;top:1368px;width:145px;height:38px;background:#fff;border:1px solid #ddd;box-shadow:0 2px 4px rgba(0,0,0,.1);font-size:13px;padding:13px 12px;font-family:"Lato",sans-serif}
.table-wrap{position:absolute;left:19px;top:230px;width:939px;height:425px;border:12px solid var(--green);border-top:0;background:var(--green)}
table{width:915px;border-collapse:collapse;font-family:"Lato",sans-serif;font-size:13px;background:#fff}
thead th{background:var(--green);color:#fff;font-family:"Montserrat",sans-serif;font-weight:500;font-size:15px;text-align:left;height:57px;padding:0 4px;position:relative;border-right:1px solid #fff;line-height:1.1}
thead th::after{content:"";position:absolute;right:8px;top:26px;border:4px solid transparent;border-top:5px solid #fff}
thead th:last-child{border-right:0}
tbody td{height:66px;border-right:1px solid var(--line);border-bottom:1px solid var(--line);text-align:center;color:#222;line-height:1.5}
tbody tr:last-child td{height:87px;border-bottom:0}
tbody td:first-child{text-align:left;padding-left:22px;padding-right:12px}
tbody td:last-child{border-right:0}
td.loc{color:var(--green-text);font-size:16px;font-weight:700}
.star{color:var(--red)}
.note{position:absolute;left:0;top:685px;width:976px;text-align:center;font-family:"Lato",sans-serif;font-size:14px;color:#333}
.note .star{font-size:22px;vertical-align:6px}

/* banner */
.banner{left:0;top:2028px;width:1200px;height:409px;background:linear-gradient(90deg,#8c7a4a 0%,#b69a3a 25%,#a7a399 50%,#d8d8d2 75%,#e6e6e0 100%)}
.banner-frame{left:764px;top:2093px;width:246px;height:277px;border:12px solid #fff}
.banner-text{left:650px;top:2180px;font-weight:700;font-size:38px;line-height:1.1;color:#1f1f1f}
.banner-pill{left:650px;top:2278px;background:var(--green-text);color:#fff;font-size:10px;padding:6px 10px}

/* footer */
.footer{left:0;top:2437px;width:1200px;height:180px;background:var(--dark)}
.foot-brand{left:224px;top:2488px;display:flex;align-items:center;gap:10px}
.foot-brand .brand-mark{width:40px;height:40px}
.foot-brand .brand-name{font-size:20px}
.follow{left:267px;top:2540px;display:flex;gap:5px;align-items:center;color:#ddd;font-size:12px}
.follow span{width:18px;height:18px;background:#111;border-radius:2px;display:block}
.foot-nav{left:618px;top:2506px;display:flex;gap:18px;font-size:9px;color:#ccc}
.foot-contact{left:588px;top:2541px;display:flex;align-items:center;gap:10px;font-size:10px;color:#ddd}
.ico{width:22px;height:22px;background:#111;display:flex;align-items:center;justify-content:center}
.to-top{left:1010px;top:2592px;width:36px;height:38px;background:#fff;display:flex;align-items:center;justify-content:center;border-radius:2px}
.bottom-bar{left:0;top:2617px;width:1200px;height:38px;background:var(--green);text-align:center;font-size:9px;color:#444;line-height:38px}
</style>
</head>
<body>

<div class="abs topbar"></div>
<div class="abs social-top"><span></span><span></span><span></span><span></span></div>
<div class="abs student-btn">Student Access</div>
<div class="abs search-box"><svg width="9" height="9" viewBox="0 0 10 10"><circle cx="4" cy="4" r="3" fill="none" stroke="#333" stroke-width="1.5"/><line x1="6.3" y1="6.3" x2="9" y2="9" stroke="#333" stroke-width="1.5"/></svg></div>

<header class="abs header"></header>
<div class="abs brand">
  <span class="brand-mark"></span>
  <div><div class="brand-name">RIDGELINE SAFETY</div><div class="brand-tag">SAFETY AND TRAINING</div></div>
</div>
<nav class="abs nav">
  <a class="active">Home</a><a>Courses</a><a>About Us</a><a>Funding</a><a>Location</a><a>Contact Us</a>
</nav>

<section class="abs hero" role="img" aria-label="Photo of construction workers in hard hats and hi-vis vests"></section>
<div class="abs hero-title"><h1>Training a Safety Culture</h1><p>That Counts</p></div>

<section class="abs card diff">
  <div class="card-head">THE RIDGELINE SAFETY DIFFERENCE</div>
  <p class="diff-sub">Commited To Helping Our Students Succeed.</p>
  <div class="tiles">
    <div class="tile"><div class="tile-photo" role="img" aria-label="Loader at a quarry" style="background:linear-gradient(#8d8a84,#b5a06a)"></div><div class="tile-label">All Courses</div></div>
    <div class="tile"><div class="tile-photo" role="img" aria-label="Handshake with work gloves" style="background:linear-gradient(#4b9fd8,#d9b64a)"></div><div class="tile-label">Funded Courses</div></div>
    <div class="tile"><div class="tile-photo" role="img" aria-label="Red mining truck" style="background:linear-gradient(#9d9890,#b4413a)"></div><div class="tile-label">Mining</div></div>
    <div class="tile"><div class="tile-photo" role="img" aria-label="Excavator on a dirt site" style="background:linear-gradient(#5f5a52,#a98a3e)"></div><div class="tile-label">Standard 11</div></div>
    <div class="tile"><div class="tile-photo" role="img" aria-label="Workers in safety harnesses" style="background:linear-gradient(#b8c2c6,#56606a)"></div><div class="tile-label">Work Safety At Heights</div></div>
    <div class="tile"><div class="tile-photo" role="img" aria-label="Business people at a laptop" style="background:linear-gradient(#6a6260,#2e2a2a)"></div><div class="tile-label">Corporate Clients</div></div>
    <div class="tile"><div class="tile-photo" role="img" aria-label="Group of students studying" style="background:linear-gradient(#c9b59a,#3f8fb0)"></div><div class="tile-label">Online Courses</div></div>
    <div class="tile"><div class="tile-photo" role="img" aria-label="Workers reviewing plans on site" style="background:linear-gradient(#7fb5d9,#d8d04a)"></div><div class="tile-label">RPL’s &amp; VOC’s</div></div>
    <div class="tile"><div class="tile-photo" role="img" aria-label="Worker beside yellow scissor lift" style="background:linear-gradient(#8a9098,#d9c43a)"></div><div class="tile-label">Plant &amp; Equipment</div></div>
    <div class="tile"><div class="tile-photo" role="img" aria-label="Construction worker on site" style="background:linear-gradient(#c48a4a,#4a4a48)"></div><div class="tile-label">Construction</div></div>
  </div>
</section>

<section class="abs card calendar">
  <div class="card-head">CALENDAR</div>
  <div class="filters">
    <div class="select" style="left:23px"><svg width="11" height="16" viewBox="0 0 11 16"><path d="M5.5 0C2.5 0 0 2.4 0 5.4 0 9.5 5.5 16 5.5 16S11 9.5 11 5.4C11 2.4 8.5 0 5.5 0zm0 7.6a2.2 2.2 0 110-4.4 2.2 2.2 0 010 4.4z" fill="#666"/></svg>Location</div>
    <div class="select" style="left:330px"><svg width="15" height="14" viewBox="0 0 15 14"><path d="M3 0h12l-3 14H0z" fill="#666"/><path d="M4.5 3h7M4 6h7" stroke="#fff" stroke-width="1"/></svg>Course</div>
    <div class="select" style="left:633px"><svg width="16" height="16" viewBox="0 0 16 16"><rect x="1" y="3" width="14" height="12" fill="none" stroke="#666" stroke-width="1.6"/><rect x="1" y="3" width="14" height="3" fill="#666"/><line x1="4.5" y1="1" x2="4.5" y2="4" stroke="#666" stroke-width="1.6"/><line x1="11.5" y1="1" x2="11.5" y2="4" stroke="#666" stroke-width="1.6"/></svg>Month</div>
  </div>
  <div class="table-wrap">
    <table>
      <colgroup><col style="width:220px"><col style="width:181px"><col style="width:91px"><col style="width:120px"><col style="width:99px"><col style="width:82px"><col style="width:122px"></colgroup>
      <thead><tr><th>Course code &amp; title</th><th>Course time</th><th>Time</th><th>Duration</th><th>Location</th><th>Price</th><th>CTA<br>discount price</th></tr></thead>
      <tbody>
        <tr><td>RIIHAN304D Work safely<br>at heights</td><td>Tuesday, october, 29 , 2019</td><td>8 am</td><td>1 day</td><td class="loc">Ironbark</td><td>$500</td><td>$120</td></tr>
        <tr><td>RIIHAN304D Work safely<br>at heights <span class="star">*</span></td><td>Tuesday, October, 29 , 2019</td><td>8 am</td><td>1 day</td><td class="loc">Ironbark</td><td>$500</td><td>$120</td></tr>
        <tr><td>HLTAID005 Confined space -<br>practical only (theory online)</td><td>Thursday, January, 30 , 2019</td><td>1pm</td><td>1/2 day</td><td class="loc">Ironbark</td><td>$80</td><td></td></tr>
        <tr><td>HLTAID001 First Aid -<br>practical only</td><td>Friday, November, 15 , 2019</td><td>1pm</td><td>1/2 day</td><td class="loc">Ironbark</td><td>$80</td><td></td></tr>
        <tr><td>CPCCCM208 Dogging &amp;<br>TLILIC0005 front end loader<br>BUNDLE</td><td>Monday, October, 28 , 2019</td><td>8 am</td><td>10 days</td><td class="loc">Ironbark</td><td>$2300</td><td>$1200</td></tr>
      </tbody>
    </table>
  </div>
  <p class="note"><span class="star">*</span> Limited spots left</p>
</section>
<div class="abs dropdown">Ironbark</div>

<section class="abs banner" role="img" aria-label="Photo of a large yellow mining dump truck at a quarry"></section>
<div class="abs banner-frame"></div>
<div class="abs banner-text">Training a Safety<br>Culture that Counts</div>
<div class="abs banner-pill">NOW TRAINING - Working at Heights &amp; Confined Spaces courses</div>

<footer class="abs footer"></footer>
<div class="abs foot-brand"><span class="brand-mark"></span><span class="brand-name">RIDGELINE SAFETY</span></div>
<div class="abs follow">Follow us on :-&nbsp;<span></span><span></span><span></span><span></span></div>
<div class="abs foot-nav"><span>Home</span><span>Courses</span><span>Our Services</span><span>About us</span><span>Funding</span><span>Locations</span><span>Contact us</span></div>
<div class="abs foot-contact">
  <span class="ico"><svg width="9" height="12" viewBox="0 0 11 16"><path d="M5.5 0C2.5 0 0 2.4 0 5.4 0 9.5 5.5 16 5.5 16S11 9.5 11 5.4C11 2.4 8.5 0 5.5 0zm0 7.6a2.2 2.2 0 110-4.4 2.2 2.2 0 010 4.4z" fill="#fff"/></svg></span>
  <span>18 Quarry Road, Ironbark QLD 4300</span>
  <span style="width:12px"></span>
  <span class="ico"><svg width="12" height="9" viewBox="0 0 12 9"><rect width="12" height="9" fill="#fff"/><path d="M0 0l6 5 6-5" fill="none" stroke="#111" stroke-width="1.2"/></svg></span>
  <span>info@ridgelinesafety.edu.au</span>
</div>
<div class="abs to-top"><svg width="14" height="9" viewBox="0 0 14 9"><path d="M1 8l6-6 6 6" fill="none" stroke="#222" stroke-width="2"/></svg></div>
<div class="abs bottom-bar">© Copyright All Right Reserved | Powered by Ridgeline Safety.</div>

</body>
</html>
```